Craft Flavoured Beer Family Extension Desing

We are a Canadian craft brewery looking for the design of a new line of beer we wish to launch within an existing family of products. Our beers are high craft beers that retail for a significant price. Example, 4.49$ for 500 mL vs. 1.49$ for a 500 mL Varnholt.

The line of beer that is being designed here is for a craft flavoured beer line targeted to women. This will be light tasting beers with light fruit flavors targeted to consumers who like beer but are not ready for the strong IPA which are generally found in the craft beer offerings.

The Mireille line, which is the name of this new product, is a ''cousin'' of the existing Louis-Armand Line (more info below).

Target Market(s)

60% Females 40% Males - 21 to 40 years old

Industry/Entity Type

Brewery

Requirements
Must have
• The products will be an INDIRECT family/line extension of the Louis-Armand line of products (design attached). There needs to be some similarities, but it cannot be too close. There are 3 main features on the Louis-Armand label (attached) : (1) the font used for the Logo; (2) the shape of the label; (3) the motif printed on the label.
• The shape of the label must be different than the current shape.
• However, the font of the logo (Louis-Armand) can be the same and the motif printed on the label can be used. Using one of these elements is sufficient to link this new brand with the Louis-Armand brand.
• The name of the product will be MIREILLE
Nice to have
• The bottle, the size, the ABV will be different than for the Louis-Armand beers.
• There will be 3 flavours initially : Blueberry, Grapefruit and Raspberry.
• There needs to be a back label, but if you design, you can use the exact same information as there is currently.
Should not have
• We don't want any fruit pictures or designs on the labels.

```html
<!DOCTYPE html>
<html lang="fr">
<head>
<meta charset="utf-8">
<title>Mireille — Bières aromatisées</title>
<link href="https://fonts.googleapis.com/css2?family=Oswald:wght@400;600&display=swap" rel="stylesheet">
<style>
  :root {
    --bg: #eeeeee;
    --ink: #1d1d22;
    --white: #ffffff;
    --blueberry: #1f5fae;
    --blueberry-dark: #163f78;
    --raspberry: #c41f33;
    --raspberry-dark: #861524;
    --grapefruit: #e3bf1f;
    --grapefruit-dark: #9c7f0c;
  }
  * { box-sizing: border-box; margin: 0; padding: 0; }
  html, body { width: 857px; height: 1200px; overflow: hidden; }
  body {
    background: radial-gradient(circle at 50% 40%, #fafafa 0%, var(--bg) 70%);
    font-family: "Oswald", sans-serif;
    color: var(--ink);
  }
  .range {
    width: 857px; height: 1200px;
    display: flex; justify-content: space-evenly; align-items: center;
    padding: 0 20px;
  }
  .label-set { width: 240px; display: flex; flex-direction: column; align-items: center; gap: 70px; }
  .label-set--blueberry { --main: var(--blueberry); --deep: var(--blueberry-dark); --text: var(--white); }
  .label-set--raspberry { --main: var(--raspberry); --deep: var(--raspberry-dark); --text: var(--white); }
  .label-set--grapefruit { --main: var(--grapefruit); --deep: var(--grapefruit-dark); --text: var(--ink); }

  .neck-label {
    width: 200px; height: 96px; background: var(--main);
    display: flex; align-items: center; justify-content: center;
  }
  .brand-name {
    font-family: "Oswald", sans-serif; font-weight: 600;
    color: var(--text); text-transform: uppercase; letter-spacing: 4px;
  }
  .neck-label .brand-name { font-size: 28px; }

  .body-label { position: relative; width: 240px; height: 360px; }
  .body-label__shape { position: absolute; inset: 0; }
  .body-label__content {
    position: absolute; inset: 0;
    display: flex; flex-direction: column; align-items: center;
    padding-top: 62px;
  }
  .marks { display: flex; gap: 10px; margin-bottom: 14px; }
  .marks span { width: 8px; height: 8px; background: var(--text); border-radius: 50%; }
  .body-label .brand-name { font-size: 40px; line-height: 58px; }
  .flavour {
    margin-top: 14px; width: 180px; padding: 4px 0;
    border-top: 2px solid var(--text); border-bottom: 2px solid var(--text);
    color: var(--text); text-align: center;
    font-weight: 600; font-size: 20px; letter-spacing: 4px; text-transform: uppercase;
  }
  .origin { margin-top: 12px; color: var(--text); font-size: 11px; letter-spacing: 2px; text-transform: uppercase; }
  .specs { margin-top: 4px; display: flex; gap: 16px; color: var(--text); font-size: 11px; letter-spacing: 1px; }
  .ornament {
    margin-top: 16px; width: 110px; height: 30px; border-radius: 15px;
    background: linear-gradient(90deg, transparent, var(--deep), transparent);
  }
  .volume { margin-top: 10px; color: var(--text); font-size: 12px; letter-spacing: 2px; }
</style>
</head>
<body>
<main class="range">

  <section class="label-set label-set--blueberry">
    <div class="neck-label"><span class="brand-name">Mireille</span></div>
    <div class="body-label">
      <svg class="body-label__shape" viewBox="0 0 240 360" aria-hidden="true">
        <path d="M0 44 L120 0 L240 44 L240 360 L0 360 Z" fill="var(--main)"/>
        <path d="M10 50 L120 11 L230 50 L230 350 L10 350 Z" fill="none" stroke="var(--text)" stroke-width="2"/>
      </svg>
      <div class="body-label__content">
        <div class="marks"><span></span><span></span><span></span></div>
        <span class="brand-name">Mireille</span>
        <div class="flavour">Blueberry</div>
        <div class="origin">Brassée au Québec</div>
        <div class="specs"><span>341 ML / 11.5 OZ</span><span>5% ALC./VOL.</span></div>
        <div class="ornament" role="img" aria-label="Ornement décoratif"></div>
        <div class="volume">341 ML</div>
      </div>
    </div>
  </section>

  <section class="label-set label-set--raspberry">
    <div class="neck-label"><span class="brand-name">Mireille</span></div>
    <div class="body-label">
      <svg class="body-label__shape" viewBox="0 0 240 360" aria-hidden="true">
        <path d="M0 44 L120 0 L240 44 L240 360 L0 360 Z" fill="var(--main)"/>
        <path d="M10 50 L120 11 L230 50 L230 350 L10 350 Z" fill="none" stroke="var(--text)" stroke-width="2"/>
      </svg>
      <div class="body-label__content">
        <div class="marks"><span></span><span></span><span></span></div>
        <span class="brand-name">Mireille</span>
        <div class="flavour">Raspberry</div>
        <div class="origin">Brassée au Québec</div>
        <div class="specs"><span>341 ML / 11.5 OZ</span><span>5% ALC./VOL.</span></div>
        <div class="ornament" role="img" aria-label="Ornement décoratif"></div>
        <div class="volume">341 ML</div>
      </div>
    </div>
  </section>

  <section class="label-set label-set--grapefruit">
    <div class="neck-label"><span class="brand-name">Mireille</span></div>
    <div class="body-label">
      <svg class="body-label__shape" viewBox="0 0 240 360" aria-hidden="true">
        <path d="M0 44 L120 0 L240 44 L240 360 L0 360 Z" fill="var(--main)"/>
        <path d="M10 50 L120 11 L230 50 L230 350 L10 350 Z" fill="none" stroke="var(--text)" stroke-width="2"/>
      </svg>
      <div class="body-label__content">
        <div class="marks"><span></span><span></span><span></span></div>
        <span class="brand-name">Mireille</span>
        <div class="flavour">Grapefruit</div>
        <div class="origin">Brassée au Québec</div>
        <div class="specs"><span>341 ML / 11.5 OZ</span><span>5% ALC./VOL.</span></div>
        <div class="ornament" role="img" aria-label="Ornement décoratif"></div>
        <div class="volume">341 ML</div>
      </div>
    </div>
  </section>

</main>
</body>
</html>
```